Award-winnning Estate Agent needs a premium version of their 'For Sale' board design

We need a premium option for our 'For Sale' board design. We have a standard board that is attached to this brief, but were are looking to have a premium design version that we will use when selling exclusive properties. Our company name is Harbourline Vale Estates and the name for this is exclusive selection is: 'The Harbourline Collection'. The design needs to work with our current brand, but have a distinctive PREMIUM feel to it. I have uploaded the barnd guidelines and also some of the exisisting logo variations. We do NOT need a new logo but feel free to play around with colours, fonts, sizes etc. for the sign.

Target Market(s)

Property buyers & house hunters

Industry/Entity Type

Real Estate - Residential Property

Font styles to use
Sans Serif

Requirements
Must have
• A premium fee, must be square design, must be easy to read when driving past the sign
Nice to have
• I'm open ot ideas

```html
<!DOCTYPE html>
<html lang="en">
<head>
<meta charset="utf-8">
<title>For Sale Board – The Harbourline Collection</title>
<link rel="stylesheet" href="https://fonts.googleapis.com/css2?family=Figtree:wght@500;600;700;800&display=swap">
<style>
  :root {
    --navy: #163764;
    --sky: #72cedd;
    --white: #ffffff;
  }
  * { margin: 0; padding: 0; box-sizing: border-box; }
  html, body {
    width: 1200px;
    height: 1199px;
    overflow: hidden;
    background: var(--white);
  }
  .board {
    position: relative;
    width: 1200px;
    height: 1199px;
    background: var(--white);
    font-family: "Figtree", Arial, sans-serif;
    color: var(--navy);
  }
  .board__headline {
    position: absolute;
    top: 132px;
    left: 0;
    width: 100%;
    text-align: center;
    font-size: 150px;
    font-weight: 800;
    letter-spacing: 2px;
    line-height: 1;
  }
  .brand-mark {
    position: absolute;
    top: 400px;
    left: 50%;
    width: 240px;
    height: 240px;
    margin-left: -120px;
    border-radius: 50%;
    background: var(--navy);
  }
  .brand-band {
    position: absolute;
    top: 585px;
    left: 0;
    width: 100%;
    height: 325px;
    background: var(--navy);
    border-top: 10px solid var(--sky);
  }
  .brand-band__name {
    position: absolute;
    top: 112px;
    left: 0;
    width: 100%;
    text-align: center;
    color: var(--white);
    font-size: 80px;
    font-weight: 600;
    line-height: 1.2;
    letter-spacing: 0.5px;
  }
  .contact-phone {
    position: absolute;
    top: 958px;
    left: 0;
    width: 100%;
    display: flex;
    align-items: center;
    justify-content: center;
    gap: 26px;
  }
  .contact-phone__icon { width: 88px; height: 88px; }
  .contact-phone__number {
    font-size: 112px;
    font-weight: 700;
    line-height: 1;
    letter-spacing: 1px;
  }
  .web-strip {
    position: absolute;
    top: 1080px;
    left: 0;
    width: 100%;
    height: 76px;
    background: var(--sky);
    display: flex;
    align-items: center;
    justify-content: center;
  }
  .web-strip__url {
    font-size: 32px;
    font-weight: 700;
    letter-spacing: 3.5px;
    text-transform: uppercase;
  }
</style>
</head>
<body>
  <main class="board">
    <h1 class="board__headline">FOR SALE</h1>

    <div class="brand-mark" aria-hidden="true"></div>

    <section class="brand-band">
      <p class="brand-band__name">The Harbourline Collection</p>
    </section>

    <div class="contact-phone">
      <svg class="contact-phone__icon" viewBox="0 0 24 24" aria-hidden="true">
        <path fill="#163764" d="M6.6 10.8c1.4 2.8 3.8 5.1 6.6 6.6l2.2-2.2c.3-.3.7-.4 1-.2 1.1.4 2.3.6 3.6.6.6 0 1 .4 1 1V20c0 .6-.4 1-1 1C10.6 21 3 13.4 3 4c0-.6.4-1 1-1h3.5c.6 0 1 .4 1 1 0 1.3.2 2.5.6 3.6.1.3 0 .7-.2 1l-2.3 2.2z"/>
      </svg>
      <span class="contact-phone__number">01632 960418</span>
    </div>

    <div class="web-strip">
      <span class="web-strip__url">www.harbourlinevaleestates.co.uk</span>
    </div>
  </main>
</body>
</html>
```